Website for Torvel Capital - investment banking firm

We have a corporate identity (thanks to Ravinka/31842) and want to extend that into a website design.  See the attached zipped files.
We have software folks in-house to do the coding.
See the attached Project Brief & Notes for more details.  Don't worry about the actual text - lorem ipsum will be fine.
The server will be Apache.
Thank you!
Desmond

Industry/Entity Type
Investment

```html
<!DOCTYPE html>
<html lang="en">
<head>
<meta charset="utf-8">
<title>Torvel Capital</title>
<link rel="stylesheet" href="https://fonts.googleapis.com/css2?family=Lato:ital,wght@0,400;0,700;1,400&family=Tinos&display=swap">
<style>
:root{
  --navy:#1f4e8f;
  --navy-dark:#173d73;
  --blue-text:#2a5594;
  --ink:#222;
  --body:#444;
  --muted:#666;
  --panel:#f3f3f1;
  --line:#cfcfcf;
  --white:#fff;
}
*{box-sizing:border-box;margin:0;padding:0}
html,body{width:1200px;height:971px;overflow:hidden}
body{position:relative;font-family:'Lato',sans-serif;color:var(--body);background:var(--panel)}
.abs{position:absolute}
.header{left:0;top:0;width:1200px;height:94px;background:linear-gradient(#fafafa,#e8e9ea)}
.brand{left:132px;top:12px;display:flex;align-items:center;gap:12px}
.brand-mark{width:60px;height:60px;background:var(--navy)}
.brand-name{font-family:'Lato',sans-serif;font-size:36px;color:var(--navy);letter-spacing:1px}
.contact-top{top:12px;display:flex;align-items:center;gap:8px;font-weight:700;color:var(--navy)}
.contact-top svg{flex:none}
.contact-top.mail{left:718px;font-size:13px}
.contact-top.phone{left:900px;font-size:19px;letter-spacing:.5px}
.nav{left:498px;top:57px;display:flex;align-items:center;font-size:14px;color:var(--ink)}
.nav a{color:inherit;text-decoration:none;padding:0 13px;line-height:26px;border-left:1px solid #aaa}
.nav a:first-child{border-left:0}
.nav a.active{background:var(--navy);color:var(--white);padding:0 16px}
.hero{left:0;top:94px;width:1200px;height:474px;background:linear-gradient(180deg,#8d9596 0%,#6a7374 45%,#4f5859 75%,#6b7374 100%)}
.hero-band{left:239px;top:256px;width:802px;height:103px;background:rgba(40,40,40,.55);color:var(--white);font-family:'Tinos',serif;font-size:28px;line-height:43px;text-align:center;padding-top:7px}
.card{top:527px;width:288px;height:148px;background:linear-gradient(#fff 0%,#f6f6f5 40%,var(--panel) 100%);border-radius:6px 6px 0 0;box-shadow:0 -2px 6px rgba(0,0,0,.08)}
.card h2{position:absolute;left:56px;top:6px;font-family:'Tinos',serif;font-weight:400;font-size:25px;color:var(--ink)}
.card h2 span{color:var(--blue-text)}
.card .tag{position:absolute;left:14px;top:6px;width:30px;height:30px;border:3px solid var(--navy);border-radius:50%}
.card .icon{position:absolute;left:16px;top:53px;width:58px;height:58px;border:2px solid #333;border-radius:50%;display:flex;align-items:center;justify-content:center}
.card .text{position:absolute;left:90px;top:51px;width:188px;max-height:82px;overflow:hidden;font-size:13px;line-height:20px;color:var(--body)}
.card .more{position:absolute;left:90px;top:143px;font-size:11.5px;font-weight:700;color:var(--navy);line-height:14px}
.card ul{list-style:none;max-height:none}
.card li{position:relative;padding-left:14px;line-height:16px;margin-bottom:6px}
.card li::before{content:"";position:absolute;left:0;top:4px;border-left:5px solid #999;border-top:4px solid transparent;border-bottom:4px solid transparent}
.news-title{font-weight:700;color:var(--ink)}
.divider{left:160px;top:705px;width:880px;height:1px;background:linear-gradient(90deg,transparent,var(--line) 15%,var(--line) 85%,transparent)}
.testi-label{left:134px;top:730px;width:135px;text-align:right;font-family:'Tinos',serif;font-size:25px;line-height:30px;color:var(--ink)}
.testi-label span{color:var(--blue-text)}
.testi-arrow{left:285px;top:720px}
.quote{left:339px;top:732px;width:710px;font-style:italic;font-size:14px;line-height:20px;color:var(--ink)}
.quote .mark{font-family:'Tinos',serif;font-size:34px;color:#aaa;line-height:0;vertical-align:-10px;font-style:normal}
.author{left:339px;top:780px;font-style:italic;font-size:14px;color:var(--navy)}
.footer{left:0;top:826px;width:1200px;height:145px;background:var(--navy);color:var(--white)}
.footer h3{position:absolute;font-size:17px;font-weight:700}
.footer .rule{position:absolute;height:1px;background:rgba(255,255,255,.3)}
.addr{left:155px;top:55px;font-size:12.5px;line-height:20px;color:#e6ecf5}
.f-item{display:flex;align-items:center;gap:12px;font-weight:700;font-size:13.5px}
.newsletter{left:554px;top:60px;display:flex}
.newsletter .field{width:206px;height:28px;background:var(--navy-dark);font-style:italic;font-size:12px;color:#b8c6dc;padding:6px 10px}
.newsletter .go{width:38px;height:28px;background:#f1f1f1;color:var(--navy);font-weight:700;font-size:15px;text-align:center;line-height:28px}
.follow{left:554px;top:108px;display:flex;align-items:center;gap:9px;font-weight:700;font-size:15px}
.follow .soc{width:29px;height:29px;border:2px solid var(--white);border-radius:50%}
.badge{left:916px;top:800px;width:108px;height:82px;background:#efefef;border-radius:0 0 54px 54px;display:flex;justify-content:center;align-items:center}
.badge div{width:62px;height:62px;border:5px solid var(--navy);border-radius:50%}
.copy{left:860px;top:904px;width:220px;text-align:center;font-size:13.5px;line-height:20px;color:#e6ecf5}
</style>
</head>
<body>
<header class="abs header">
  <div class="abs brand"><div class="brand-mark"></div><div class="brand-name">Torvel Capital</div></div>
  <div class="abs contact-top mail">
    <svg width="30" height="22" viewBox="0 0 30 22"><rect x="1" y="1" width="24" height="20" rx="3" fill="#fff" stroke="#555"/><rect x="6" y="6" width="14" height="10" fill="#333"/><path d="M6 6l7 5 7-5" stroke="#fff" fill="none"/><path d="M25 8l4 3-4 3" fill="#fff" stroke="#555"/></svg>
    info@torvelcapital.com
  </div>
  <div class="abs contact-top phone">
    <svg width="30" height="22" viewBox="0 0 30 22"><rect x="1" y="1" width="24" height="20" rx="3" fill="#fff" stroke="#555"/><rect x="9" y="4" width="8" height="14" rx="1" fill="#333"/><path d="M25 8l4 3-4 3" fill="#fff" stroke="#555"/></svg>
    214-555-0187
  </div>
  <nav class="abs nav">
    <a class="active" href="#">About</a>
    <a href="#">Services</a>
    <a href="#">Current Engagements</a>
    <a href="#">Completed Transactions</a>
    <a href="#">Contact Us</a>
  </nav>
</header>

<div class="abs hero" role="img" aria-label="Rowing crew photographed from above on dark rippled water"></div>
<div class="abs hero-band">Private Investment Banking Advisory Firm That Acts As An<br>Intermediary On Behalf Of Buyers &amp; Sellers Of Private Companies.</div>

<section class="abs card" style="left:134px">
  <div class="tag"></div>
  <h2><span>Who</span> We Are</h2>
  <div class="icon"><svg width="30" height="30" viewBox="0 0 30 30"><circle cx="15" cy="9" r="7" fill="#333"/><path d="M2 29c0-9 6-12 13-12s13 3 13 12z" fill="#333"/></svg></div>
  <p class="text" style="letter-spacing:.3px;text-align:justify">Torvel Capital's history in mergers and acquisitions traces back to 1998. We pride our selves in successfully</p>
  <span class="more">READ MORE »</span>
</section>

<section class="abs card" style="left:456px">
  <div class="tag"></div>
  <h2><span>What</span> We Do</h2>
  <div class="icon"><svg width="34" height="30" viewBox="0 0 34 30"><circle cx="12" cy="18" r="8" fill="none" stroke="#333" stroke-width="5" stroke-dasharray="4 2"/><circle cx="25" cy="8" r="5" fill="none" stroke="#333" stroke-width="4" stroke-dasharray="3 2"/></svg></div>
  <ul class="text" style="top:55px">
    <li>Buy-Side Acquisitions</li>
    <li>Recapitalizations &amp; Growth Capital Partnerships</li>
    <li>Sell-Side Transactions</li>
  </ul>
  <span class="more">READ MORE »</span>
</section>

<section class="abs card" style="left:778px">
  <div class="tag"></div>
  <h2><span>Latest</span> News</h2>
  <div class="icon"><svg width="32" height="28" viewBox="0 0 32 28"><rect x="2" y="9" width="8" height="10" fill="#333"/><path d="M10 9l16-7v24l-16-7z" fill="#333"/><rect x="4" y="19" width="5" height="7" fill="#333"/></svg></div>
  <div class="text"><p class="news-title">Kauitm veleum iriure lorrfu</p><p>Hdrehrit in vulptate velit essehi molestie coequa. molestie uitmi veleum iriure lorrfu hdrehrit</p></div>
  <span class="more">READ MORE »</span>
</section>

<div class="abs divider"></div>
<div class="abs testi-label"><span>Client</span><br>Testimonials</div>
<svg class="abs testi-arrow" width="30" height="78" viewBox="0 0 30 78"><path d="M0 0l28 39L0 78z" fill="#e4e4e2"/></svg>
<p class="abs quote"><span class="mark">“</span> Lorem ipsum sit amet consectet uradi incididunt ut labore et dolore magna aliquaps enimi ad minim veniam quiidunt ut labore etpvloore magn incididunt ut labore et dolore na aliquatmp enimt ad minim veniam quiidunt ut labore <span class="mark">”</span></p>
<p class="abs author">Mr. Dolore na Aliqua</p>

<footer class="abs footer">
  <h3 style="left:133px;top:13px">Contact Info</h3>
  <div class="rule" style="left:133px;top:43px;width:366px"></div>
  <svg class="abs" style="left:133px;top:59px" width="12" height="16" viewBox="0 0 12 16"><path d="M6 0a6 6 0 0 1 6 6c0 4-6 10-6 10S0 10 0 6a6 6 0 0 1 6-6z" fill="#cbd6e6"/><circle cx="6" cy="6" r="2.2" fill="#1f4e8f"/></svg>
  <p class="abs addr">Hong Kong: Room 1804<br>Harbourline Centre<br>12 - 18 Lockhart Row East<br>Wanchai, Hong Kong</p>
  <div class="abs f-item" style="left:337px;top:55px"><svg width="10" height="16" viewBox="0 0 10 16"><rect x="1" y="1" width="8" height="14" rx="1.5" fill="none" stroke="#cbd6e6" stroke-width="1.5"/></svg>214-555-0187</div>
  <div class="abs f-item" style="left:337px;top:88px;font-size:12.5px"><svg width="14" height="10" viewBox="0 0 14 10"><rect x=".5" y=".5" width="13" height="9" fill="#cbd6e6"/><path d="M.5 .5l6.5 5 6.5-5" stroke="#1f4e8f" fill="none"/></svg>info@torvelcapital.com</div>
  <h3 style="left:554px;top:13px">Newsletter Signup</h3>
  <div class="rule" style="left:554px;top:43px;width:241px"></div>
  <div class="abs newsletter"><div class="field">Enter your email</div><div class="go">GO</div></div>
  <div class="abs follow">Follow Us On:<span class="soc"></span><span class="soc"></span><span class="soc"></span><span class="soc"></span></div>
</footer>
<div class="abs badge"><div></div></div>
<p class="abs copy">© Copyright 2014 Torvel Capital.<br>All Rights Reserved</p>
</body>
</html>
```